new construction company branding

branding

Can I have a banner made so I can hang it as 1) branding my jobsite 2) advertisement

Target Market(s)

Commercial

Industry/Entity Type

Construction Trade

Font styles to use
Other font styles liked:
• Cinzel bold

Colors
EB3D1F
EC4F4E
F09395
F8D3D4
FCEDEE

Requirements
Must have
• Bright colors for advertisement
Nice to have
• 36”x48” canvas
Should not have
• To busy

```html
<!DOCTYPE html>
<html lang="en">
<head>
<meta charset="UTF-8">
<title>Keystone Build Co — Jobsite Banner</title>
<link href="https://fonts.googleapis.com/css2?family=Anton&family=Cinzel:wght@700;900&family=Montserrat:wght@500;600;700&display=swap" rel="stylesheet">
<style>
  :root {
    --stage: #d0d0d0;
    --paper: #ffffff;
    --ink: #222222;
    --red: #e10f14;
    --grey-name: #c9c9c9;
    --white: #ffffff;
  }
  * { margin: 0; padding: 0; box-sizing: border-box; }
  html, body {
    width: 1200px; height: 720px; overflow: hidden;
    background: var(--stage);
  }
  .banner {
    position: absolute; left: 140px; top: 15px;
    width: 920px; height: 690px;
    background: var(--paper);
    overflow: hidden;
  }
  .banner__texture {
    position: absolute; inset: 0;
    background:
      linear-gradient(180deg, rgba(255,255,255,0) 0%, rgba(255,255,255,0.9) 30%, rgba(255,255,255,0.9) 60%, rgba(255,255,255,0) 100%),
      linear-gradient(135deg, #f4f4f4 0%, #e6e6e6 50%, #f2f2f2 100%);
  }
  .brand {
    position: absolute; left: 0; right: 0; top: 40px;
    text-align: center;
  }
  .brand__mark {
    width: 64px; height: 64px; border-radius: 50%;
    background: var(--red);
    margin: 0 auto 18px;
  }
  .brand__name {
    font-family: 'Cinzel', serif; font-weight: 700;
    font-size: 36px; color: var(--grey-name);
    letter-spacing: 1px; line-height: 1; white-space: nowrap;
  }
  .brand__role {
    margin-top: 22px;
    font-family: 'Cinzel', serif; font-weight: 900;
    font-size: 26px; color: var(--red);
    letter-spacing: 9px; line-height: 1; white-space: nowrap;
  }
  .headline {
    position: absolute; left: 79px; width: 752px;
    text-align: center; line-height: 1; white-space: nowrap;
  }
  .headline--dark {
    top: 250px;
    font-family: 'Anton', sans-serif; font-size: 100px;
    color: var(--ink); letter-spacing: -1px;
    transform: scaleY(0.93);
  }
  .headline--red {
    top: 356px;
    font-family: 'Montserrat', sans-serif; font-weight: 600;
    font-size: 80px; color: var(--red); letter-spacing: 0;
  }
  .license {
    position: absolute; left: 79px; top: 443px;
    width: 752px; height: 42px;
    background: var(--ink); color: var(--white);
    font-family: 'Montserrat', sans-serif; font-weight: 500;
    font-size: 28px; text-align: center; line-height: 42px;
    white-space: nowrap;
  }
  .footer-shapes { position: absolute; inset: 0; }
  .contact {
    position: absolute; color: var(--white);
    font-family: 'Montserrat', sans-serif;
    display: flex; align-items: center; white-space: nowrap;
  }
  .contact--phone {
    left: 20px; top: 606px; height: 62px;
    font-weight: 700; font-size: 52px; gap: 8px;
  }
  .contact--web {
    left: 475px; top: 637px; height: 32px;
    font-weight: 600; font-size: 23px; gap: 8px;
  }
</style>
</head>
<body>
  <main class="banner">
    <div class="banner__texture" role="img" aria-label="Soft grey faceted geometric background texture"></div>

    <header class="brand">
      <div class="brand__mark"></div>
      <div class="brand__name">KEYSTONE BUILD CO LLC</div>
      <div class="brand__role">General Contractor</div>
    </header>

    <h1 class="headline headline--dark">TOGETHER ACHIEVING</h1>
    <h2 class="headline headline--red">COMMON GOALS</h2>

    <p class="license">License b no #2048371 Bonded/insured</p>

    <svg class="footer-shapes" width="920" height="690" viewBox="0 0 920 690" aria-hidden="true">
      <polygon points="0,602 494,602 415,670 0,670" fill="#222222"/>
      <polygon points="458,670 500,636 900,636 860,670" fill="#e10f14"/>
      <polygon points="920,500 920,545 745,690 700,690 720,670" fill="#e10f14"/>
      <polygon points="920,590 920,690 830,690" fill="#222222"/>
    </svg>

    <div class="contact contact--phone">
      <svg width="22" height="42" viewBox="0 0 22 42" aria-hidden="true">
        <rect x="1.5" y="1.5" width="19" height="39" rx="3" fill="none" stroke="#ffffff" stroke-width="3"/>
        <rect x="4" y="6" width="14" height="28" fill="#ffffff"/>
      </svg>
      <span>123-4567-890</span>
    </div>

    <div class="contact contact--web">
      <svg width="16" height="16" viewBox="0 0 16 16" aria-hidden="true">
        <circle cx="8" cy="8" r="7" fill="none" stroke="#ffffff" stroke-width="1.6"/>
        <ellipse cx="8" cy="8" rx="3" ry="7" fill="none" stroke="#ffffff" stroke-width="1.3"/>
        <line x1="1" y1="8" x2="15" y2="8" stroke="#ffffff" stroke-width="1.3"/>
      </svg>
      <span>www.yourwebsiet.com</span>
    </div>
  </main>
</body>
</html>
```